Business Card Design Project - 2 sided

We need a business card design for a card having one business on each side (ie. two businesses on one card). Would like a design that incorporates logo, tagline and normal fields (name, position, address, phone).

Would also like an allowance for small font text along the bottom (text to be determined, but less than 50 characters).

NB. Attached logo for Harbor Quill has two variations - either can be used.

www.harborquill-example.com / www.velmaro-example.com

```html
<!DOCTYPE html>
<html lang="en">
<head>
<meta charset="utf-8">
<title>Harbor Quill / Velmaro – Business Card</title>
<link rel="stylesheet" href="https://fonts.googleapis.com/css2?family=Source+Sans+3:wght@400;600;700&display=swap">
<style>
  :root {
    --backdrop: #d9d4ce;
    --card: #ffffff;
    --ink: #3f3f3f;
    --ink-soft: #555555;
    --rule: #c9c9c9;
    --green: #7cbd3a;
    --navy: #2f2a6b;
    --blue: #2b86c5;
    --font: "Source Sans 3", "Myriad Pro", Arial, sans-serif;
  }
  * { box-sizing: border-box; margin: 0; padding: 0; }
  html, body { width: 1200px; height: 402px; overflow: hidden; }
  body {
    background: var(--backdrop);
    font-family: var(--font);
    color: var(--ink);
    position: relative;
  }
  .card {
    position: absolute;
    top: 56px;
    width: 512px;
    height: 290px;
    background: var(--card);
    box-shadow: 0 2px 6px rgba(0,0,0,.18);
  }
  .card--harbor { left: 62px; }
  .card--velmaro { left: 625px; }

  .brand {
    position: absolute;
    top: 42px;
    left: 0; right: 0;
    display: flex;
    align-items: center;
    justify-content: center;
    gap: 12px;
  }
  .brand__dot { width: 34px; height: 34px; border-radius: 50%; }
  .brand__name { font-size: 44px; font-weight: 600; letter-spacing: .5px; line-height: 1; }
  .card--harbor .brand__dot { background: var(--green); }
  .card--harbor .brand__name { color: var(--navy); }
  .card--velmaro .brand__dot { background: var(--green); }
  .card--velmaro .brand__name { color: var(--blue); }

  .tagline {
    position: absolute;
    left: 0; right: 0;
    text-align: center;
    color: var(--ink);
  }
  .card--harbor .tagline { top: 120px; font-size: 12px; font-weight: 600; }
  .card--velmaro .tagline { top: 112px; font-size: 16px; font-weight: 400; letter-spacing: .4px; }

  .person {
    position: absolute;
    top: 164px;
    left: 0; right: 0;
    text-align: center;
  }
  .person__name { font-size: 16px; font-weight: 700; color: var(--ink); }
  .person__title { font-size: 13px; color: var(--ink-soft); }

  .divider {
    position: absolute;
    top: 196px;
    left: 136px;
    width: 240px;
    height: 2px;
    background: linear-gradient(90deg, transparent, var(--green) 50%, transparent);
    opacity: .55;
  }

  .contact {
    position: absolute;
    top: 208px;
    left: 50px;
    display: flex;
    font-size: 13px;
    line-height: 18px;
    color: var(--ink);
  }
  .contact__col { padding: 0 10px; border-left: 1px solid var(--rule); }
  .contact__col:first-child { padding-left: 0; border-left: 0; }
  .contact__row { display: flex; align-items: center; gap: 5px; }
  .contact__row svg { width: 10px; height: 10px; flex: none; }

  .fineprint {
    position: absolute;
    top: 262px;
    left: 0; right: 0;
    text-align: center;
    font-size: 10px;
    letter-spacing: .2px;
    color: var(--ink);
  }

  .band {
    position: absolute;
    left: 0; bottom: 0;
    width: 512px;
    height: 12px;
    display: block;
  }
</style>
</head>
<body>

<section class="card card--harbor" aria-label="Harbor Quill side">
  <div class="brand">
    <span class="brand__dot"></span>
    <span class="brand__name">Harbor Quill</span>
  </div>
  <p class="tagline">Website Translation and Localisation Specialist...</p>
  <p class="person"><span class="person__name">Your Name</span> <span class="person__title">/ Title</span></p>
  <div class="divider"></div>
  <div class="contact">
    <div class="contact__col">
      <div class="contact__row"><svg viewBox="0 0 10 10"><path d="M2 1l2 2-1 1.5c.6 1.2 1.3 1.9 2.5 2.5L7 6l2 2-1.5 1.5C4.5 9 1 5.5.5 2.5z" fill="var(--green)"/></svg>123-456-7890</div>
      <div class="contact__row"><svg viewBox="0 0 10 10"><rect x="2.5" y=".5" width="5" height="9" rx="1" fill="var(--green)"/><rect x="3.5" y="1.8" width="3" height="5" fill="#fff"/></svg>123-456-7890</div>
    </div>
    <div class="contact__col">
      <div class="contact__row"><svg viewBox="0 0 10 10"><rect x=".5" y="2" width="9" height="6.5" rx="1" fill="var(--green)"/><path d="M1 2.5l4 3 4-3" stroke="#fff" stroke-width=".9" fill="none"/></svg>name@website.com</div>
      <div class="contact__row"><svg viewBox="0 0 10 10"><circle cx="5" cy="5" r="4.5" fill="var(--green)"/><path d="M.8 5h8.4M5 .6c-2 2.6-2 6.2 0 8.8M5 .6c2 2.6 2 6.2 0 8.8" stroke="#fff" stroke-width=".7" fill="none"/></svg>www.website.com</div>
    </div>
    <div class="contact__col">
      <div>Complex name, Street</div>
      <div>City, State, zip code</div>
    </div>
  </div>
  <p class="fineprint">xxxxxxxxxxxxxxxxxxxxxxxxxxxxxxxxxxxxxxxxxxxxxxxx</p>
  <svg class="band" viewBox="0 0 512 12" preserveAspectRatio="none" aria-hidden="true">
    <polygon points="0,0 270,0 256,12 0,12" fill="var(--navy)"/>
    <polygon points="278,0 512,0 512,12 264,12" fill="var(--green)"/>
  </svg>
</section>

<section class="card card--velmaro" aria-label="Velmaro side">
  <div class="brand">
    <span class="brand__dot"></span>
    <span class="brand__name">Velmaro</span>
  </div>
  <p class="tagline">Professional SEO Services</p>
  <p class="person"><span class="person__name">Your Name</span> <span class="person__title">/ Title</span></p>
  <div class="divider"></div>
  <div class="contact">
    <div class="contact__col">
      <div class="contact__row"><svg viewBox="0 0 10 10"><path d="M2 1l2 2-1 1.5c.6 1.2 1.3 1.9 2.5 2.5L7 6l2 2-1.5 1.5C4.5 9 1 5.5.5 2.5z" fill="var(--green)"/></svg>123-456-7890</div>
      <div class="contact__row"><svg viewBox="0 0 10 10"><rect x="2.5" y=".5" width="5" height="9" rx="1" fill="var(--green)"/><rect x="3.5" y="1.8" width="3" height="5" fill="#fff"/></svg>123-456-7890</div>
    </div>
    <div class="contact__col">
      <div class="contact__row"><svg viewBox="0 0 10 10"><rect x=".5" y="2" width="9" height="6.5" rx="1" fill="var(--green)"/><path d="M1 2.5l4 3 4-3" stroke="#fff" stroke-width=".9" fill="none"/></svg>name@website.com</div>
      <div class="contact__row"><svg viewBox="0 0 10 10"><circle cx="5" cy="5" r="4.5" fill="var(--green)"/><path d="M.8 5h8.4M5 .6c-2 2.6-2 6.2 0 8.8M5 .6c2 2.6 2 6.2 0 8.8" stroke="#fff" stroke-width=".7" fill="none"/></svg>www.website.com</div>
    </div>
    <div class="contact__col">
      <div>Complex name, Street</div>
      <div>City, State, zip code</div>
    </div>
  </div>
  <p class="fineprint">xxxxxxxxxxxxxxxxxxxxxxxxxxxxxxxxxxxxxxxxxxxxxxxx</p>
  <svg class="band" viewBox="0 0 512 12" preserveAspectRatio="none" aria-hidden="true">
    <polygon points="0,0 270,0 256,12 0,12" fill="var(--blue)"/>
    <polygon points="278,0 512,0 512,12 264,12" fill="var(--green)"/>
  </svg>
</section>

</body>
</html>
```